Bifold brochure design for leadership academy

Please see below. This is a bifold brochure for a leadership academy. (www.brv.institute). Look and feel must be colours, shapes, abstract designs, graphics, pictures. Make this professional, yet casual and bold.

Feel free to design just the front and back cover, then I'll give feedback on whether or not you're in the right direction.

COVER
- Title: “The Boldest Bridge Year Journey”
- “Northward Mentor Institute” logo somewhere
- Subtitles (with images, icons, and/or shapes): “Self-discovery” “Skills development” “Real-world Impact”

PAGE 2 (Inside Fold)
- Title: "The Program"
- Section 2a: Section title: "How it works”
- Image: See website, image under "four phases of the program". Please adapt and make it look better
- Text: NMI is a structured, 8-month ‘gap year’ program for 18-25 year olds who want more than just a year off – they want a year ahead. Our aim is to develop high-potential young leaders with strong values, clear purpose, high-impact skills, and a track record of real-world accomplishments that are second-to-none. We do this through four-phases.
- Section 2b: Section title: “Dates & Timing”
- Image: See image on website under 'dates and timing'. Make sure both dates show up on the brochure (September and January program).
- Text: There are two programs per year: one that starts in September, the other in January. The first four months of the program are based in Toronto at the NMI headquarters. The curriculum we work through is highly engaging and personalized, focusing directly on students’ goals. After that, students are out in the world, achieving the remaining components of the program (e.g. internship, volunteer abroad).

PAGE 3 (Outside Fold)
- Page Title: "The Students"
- Section 3a: Section title: “Who’s it for”
- Subtitle1: “High school graduates”
 Image/icon of a high school grad
 Text1: 90% of high school grads aren't sure why they’re going to university or what they want to study.
 Text2: NMI helps students discover what they truly want to do in life, and make enormous progress towards these goals.

- Subtitle2: “Post-secondary students”
 Image/icon of a university / college student
 Text1: 28% of students switch or drop out of their program because it wasn’t for them or they didn’t like it.
 Text2: Don't keep moving around or risk switching careers down the road – find out what sparks your passion with NMI.

- Subtitle3: “Post-secondary graduates”
 Image/icon of a university/ college grad
 Text1: 50% of graduates are unemployed or underemployed, 60% are in debt.
 Text2: NMI will help you get your dream job – our students won’t settle for anything less.

- Section 3b: Section title: “How to apply”
 Text1: We select high-potential young leaders with a desire to improve themselves and impact the world.
 Text2: We won’t ask you for your grades – we care more about your values and potential.
 Text3: Visit www.brv.institute to apply now

BACK COVER
- Page Title: “Get in Touch”
- Website: www.brv.institute
- Facebook page: facebook.com/brv.institute
- Twitter handle: @brv_institute
- Email: tomas@brv.institute

Project Deadline Extended Reason: Made a mistake initially only giving designers 2 days to submit. This allows for more high quality designs. Thank you. Added Wednesday, March 18, 2015

Target Market(s)

18-25 year olds, parents, teachers

Industry/Entity Type

Leadership

Requirements
Must have
• Beautiful design - sleek and bold, yet colourful and casual. Keep the colours similar to our website (www.brv.institute). See examples of other brochures.
• http://img.pelvoro.net/jpg/00/11/22/33/240_F_11223344_xQr8LmPzTw3KdNvBsYcHuJeFa2gkTqWn.jpg
• http://vantoliq.com/wp-content/uploads/2014/11/Real-Estate-Bi-fold-Brochure.jpg
• http://www.murablo.com/media/k2/galleries/5/001-bi-fold-brochure-psd-mock-up-template.jpg
• http://img.pelvoro.net/jpg/00/44/55/66/240_F_44556677_Zk3wPqLm8RtYvBnXcDs2HjKuE5fa9Gq0.jpg

```html
<!DOCTYPE html>
<html lang="en">
<head>
<meta charset="utf-8">
<title>Northward Mentor Institute – Bifold Brochure</title>
<link rel="stylesheet" href="https://fonts.googleapis.com/css2?family=Open+Sans:wght@400;600;700;800&display=swap">
<style>
:root{
  --stage:#e9e9ea;
  --red:#b01c22;
  --red-dark:#8c1419;
  --red-light:#c9353a;
  --beige:#ecdcc1;
  --beige-soft:#f6eee1;
  --cream:#fbf7f0;
  --ink:#3c3c3c;
  --ink-soft:#6a6a6a;
  --white:#ffffff;
  --blue-head:#3d8fc6;
  --phase-green:#76a158;
  --phase-grey:#8e8e8e;
  --phase-blue:#a9cde6;
  --phase-pink:#d9a0a0;
  --row-blue:#d7ecf8;
  --row-grey:#e3e3e3;
  --row-beige:#efe0c7;
  --bar-dark:#6b6b6b;
}
*{box-sizing:border-box;margin:0;padding:0}
html,body{width:1200px;height:780px;overflow:hidden}
body{background:var(--stage);font-family:"Open Sans",Arial,sans-serif;color:var(--ink);position:relative}

.spread{position:absolute;top:186px;width:570px;height:408px;display:flex;box-shadow:0 6px 18px rgba(0,0,0,.18)}
.spread--outside{left:15px}
.spread--inside{left:615px}
.panel{position:relative;width:285px;height:408px;overflow:hidden}

/* brand name: one colour, one weight, one plain square */
.brand{display:flex;align-items:center;gap:5px;color:var(--red);font-weight:700;white-space:nowrap}
.brand__square{flex:0 0 auto;background:var(--red)}

/* back cover */
.back-cover{background:linear-gradient(180deg,var(--beige) 0%,var(--beige-soft) 100%)}
.bubble{position:absolute}
.bubble--white{left:70px;top:100px}
.bubble--red{left:128px;top:70px;width:92px;height:92px;border-radius:50%;background:var(--red);color:var(--white);display:flex;flex-direction:column;align-items:center;justify-content:center;line-height:1}
.bubble--red .small{font-size:15px;font-weight:400}
.bubble--red .big{font-size:24px;font-weight:600}
.contact-card{position:absolute;left:22px;right:22px;top:292px;height:58px;background:var(--white);border-radius:8px;display:flex;align-items:center;justify-content:space-between;padding:0 12px}
.contact-card .brand{font-size:8px}
.contact-card .brand__square{width:7px;height:7px}
.contact-list{list-style:none;font-size:6.5px;color:var(--ink);line-height:1.45}
.contact-list li{display:flex;align-items:center;gap:4px}
.contact-list .dot{width:6px;height:6px;background:var(--ink-soft);border-radius:1px;display:inline-block}
.web-band{position:absolute;left:0;right:0;bottom:14px;height:26px;background:var(--red);color:var(--white);font-size:9px;font-weight:600;letter-spacing:3px;display:flex;align-items:center;justify-content:center;border-top:3px solid var(--red-light)}
.base-strip{position:absolute;left:0;right:0;bottom:0;height:14px;background:var(--white)}

/* front cover */
.front-cover{background:linear-gradient(180deg,var(--white) 40%,var(--beige-soft) 100%)}
.cover-photo{position:absolute;left:0;top:0;width:285px;height:178px}
.title-tab{position:absolute;right:0;top:18px;height:22px;padding:0 12px 0 16px;background:var(--red);color:var(--white);font-size:10.5px;font-weight:700;display:flex;align-items:center;border-radius:11px 0 0 11px}
.pillars{position:absolute;left:18px;top:210px;width:250px;font-size:14px;font-weight:600;color:var(--ink);line-height:1.5}
.pillars li{list-style:none}
.pillars li:nth-child(2){padding-left:38px}
.pillars li:nth-child(3){padding-left:88px}
.front-cover .brand{position:absolute;left:18px;top:326px;font-size:13px}
.front-cover .brand__square{width:11px;height:11px}

/* inside shared */
.page-head{position:absolute;left:0;right:0;top:14px;height:20px;background:var(--red);color:var(--white);font-size:11px;font-weight:700;display:flex;align-items:center;padding-left:12px}
.section-title{color:var(--blue-head);font-size:10px;font-weight:700}
.body-copy{font-size:5.6px;line-height:1.4;color:var(--ink)}

/* program page */
.program{background:var(--white)}
.program .how{position:absolute;left:12px;top:40px}
.program .how .kicker{font-size:6.5px;font-weight:700;color:var(--ink);text-transform:uppercase}
.phases{position:absolute;left:12px;top:66px;width:261px;height:118px;display:flex;gap:2px}
.phase{flex:1;display:flex;flex-direction:column;color:var(--white)}
.phase__label{font-size:6px;font-weight:700;padding:3px;background:rgba(0,0,0,.18)}
.phase__art{height:40px;margin:5px 6px;border-radius:4px;background:rgba(255,255,255,.35)}
.phase__text{font-size:5px;line-height:1.35;padding:0 5px}
.phase--discover{background:var(--phase-green)}
.phase--design{background:var(--phase-grey)}
.phase--build{background:var(--phase-blue);color:var(--ink)}
.phase--achieve{background:var(--phase-pink);color:var(--ink)}
.program .intro{position:absolute;left:12px;top:190px;width:261px}
.program .dates{position:absolute;left:12px;top:240px}
.timing{position:absolute;left:12px;top:258px;width:261px;height:128px;background:var(--row-beige);display:flex;padding:6px;gap:8px}
.timing svg{flex:0 0 140px}
.timing .body-copy{flex:1}

/* students page */
.students{background:var(--white)}
.students .page-head{top:20px}
.who{position:absolute;left:12px;top:48px}
.rows{position:absolute;left:12px;top:62px;width:261px}
.row{position:relative;height:58px;padding:5px 56px 4px 8px;margin-bottom:4px}
.row--hs{background:var(--row-blue)}
.row--ps{background:var(--row-grey)}
.row--grad{background:var(--row-beige)}
.row h3{font-size:8px;font-weight:700;color:var(--ink);margin-bottom:2px}
.row--hs h3{color:var(--blue-head)}
.row .icon{position:absolute;right:8px;top:8px;width:40px;height:40px;border-radius:50%;background:linear-gradient(160deg,#2d2d2d,#777)}
.badges{position:absolute;left:100px;top:252px;display:flex;gap:8px}
.badges span{width:24px;height:14px;background:var(--row-grey)}
.badges span:last-child{background:var(--red)}
.apply{position:absolute;left:12px;top:276px;width:261px;height:116px;background:var(--row-blue);padding:6px 8px}
.apply .bar{background:var(--bar-dark);color:var(--white);font-size:5.6px;line-height:1.45;padding:4px 6px;margin:5px 0 4px;width:210px}
.apply .globe{position:absolute;right:14px;bottom:10px;width:32px;height:32px;border-radius:50%;background:radial-gradient(circle at 35% 35%,#8fc3e8,#2f6fa8)}
</style>
</head>
<body>

<section class="spread spread--outside">
  <article class="panel back-cover">
    <svg class="bubble bubble--white" width="56" height="56" viewBox="0 0 56 56" aria-hidden="true">
      <path d="M28 4a24 22 0 1 1-14 40l-8 8 3-12A24 22 0 0 1 28 4z" fill="#fff"/>
    </svg>
    <div class="bubble bubble--red"><span class="small">get in</span><span class="big">touch</span></div>
    <div class="contact-card">
      <div class="brand"><span class="brand__square"></span><span>Northward Mentor Institute</span></div>
      <ul class="contact-list">
        <li><span class="dot"></span>www.brv.institute</li>
        <li><span class="dot"></span>facebook.com/brv.institute</li>
        <li><span class="dot"></span>@brv_institute</li>
        <li><span class="dot"></span>tomas@brv.institute</li>
      </ul>
    </div>
    <div class="web-band">www.brv.institute</div>
    <div class="base-strip"></div>
  </article>

  <article class="panel front-cover">
    <svg class="cover-photo" viewBox="0 0 285 178" role="img" aria-label="Photo of hands holding a globe">
      <defs>
        <linearGradient id="photoTone" x1="0" y1="0" x2="1" y2="1">
          <stop offset="0" stop-color="#d9c7a8"/><stop offset=".55" stop-color="#3f86c4"/><stop offset="1" stop-color="#cfe2ef"/>
        </linearGradient>
      </defs>
      <path d="M0 0H285V150Q170 196 0 150Z" fill="url(#photoTone)"/>
      <path d="M0 150Q170 196 285 150" fill="none" stroke="#b01c22" stroke-width="5"/>
    </svg>
    <div class="title-tab">The Boldest Bridge Year Journey</div>
    <ul class="pillars">
      <li>Self-discovery</li>
      <li>Skills development</li>
      <li>Real-world Impact</li>
    </ul>
    <div class="brand"><span class="brand__square"></span><span>Northward Mentor Institute</span></div>
    <div class="web-band">www.brv.institute</div>
    <div class="base-strip"></div>
  </article>
</section>

<section class="spread spread--inside">
  <article class="panel program">
    <header class="page-head">The Program</header>
    <div class="how">
      <h2 class="section-title">How it works</h2>
      <p class="kicker">Four phases of the program</p>
    </div>
    <div class="phases">
      <div class="phase phase--discover"><span class="phase__label">1. Discover</span><div class="phase__art"></div><p class="phase__text">Find your values, strengths and purpose.</p></div>
      <div class="phase phase--design"><span class="phase__label">2. Design</span><div class="phase__art"></div><p class="phase__text">Map a personal plan with clear goals.</p></div>
      <div class="phase phase--build"><span class="phase__label">3. Build</span><div class="phase__art"></div><p class="phase__text">Grow high-impact skills with mentors.</p></div>
      <div class="phase phase--achieve"><span class="phase__label">4. Achieve</span><div class="phase__art"></div><p class="phase__text">Deliver real results out in the world.</p></div>
    </div>
    <p class="body-copy intro">NMI is a structured, 8-month ‘gap year’ program for 18-25 year olds who want more than just a year off – they want a year ahead. Our aim is to develop high-potential young leaders with strong values, clear purpose, high-impact skills, and a track record of real-world accomplishments that are second-to-none. We do this through four-phases.</p>
    <h2 class="section-title dates">Dates &amp; Timing</h2>
    <div class="timing">
      <svg viewBox="0 0 140 116" aria-label="Program timeline chart">
        <g font-family="Open Sans, Arial, sans-serif" font-size="5" fill="#3c3c3c">
          <text x="0" y="8">Sep</text><text x="17" y="8">Oct</text><text x="34" y="8">Nov</text><text x="51" y="8">Dec</text><text x="68" y="8">Jan</text><text x="85" y="8">Feb</text><text x="102" y="8">Mar</text><text x="119" y="8">Apr</text>
        </g>
        <line x1="0" y1="12" x2="140" y2="12" stroke="#8e8e8e" stroke-width=".6"/>
        <rect x="0" y="20" width="68" height="7" fill="#3d8fc6"/>
        <rect x="68" y="20" width="72" height="7" fill="#a9cde6"/>
        <rect x="68" y="58" width="68" height="7" fill="#b01c22"/>
        <rect x="0" y="58" width="68" height="7" fill="#d9a0a0"/>
        <g font-family="Open Sans, Arial, sans-serif" font-size="5.5" font-weight="700" fill="#3c3c3c">
          <text x="0" y="38">September program</text>
          <text x="0" y="76">January program</text>
        </g>
        <g font-family="Open Sans, Arial, sans-serif" font-size="5" fill="#6a6a6a">
          <text x="0" y="46">Toronto, then out in the world</text>
          <text x="0" y="84">Toronto, then out in the world</text>
        </g>
        <circle cx="5" cy="100" r="4" fill="#b01c22"/><text x="12" y="102" font-family="Open Sans, Arial, sans-serif" font-size="5" fill="#3c3c3c">Based at headquarters</text>
        <circle cx="5" cy="110" r="4" fill="#3d8fc6"/><text x="12" y="112" font-family="Open Sans, Arial, sans-serif" font-size="5" fill="#3c3c3c">Internship &amp; volunteering</text>
      </svg>
      <p class="body-copy">There are two programs per year: one that starts in September, the other in January. The first four months of the program are based in Toronto at the NMI headquarters. The curriculum we work through is highly engaging and personalized, focusing directly on students’ goals. After that, students are out in the world, achieving the remaining components of the program (e.g. internship, volunteer abroad).</p>
    </div>
  </article>

  <article class="panel students">
    <header class="page-head">The Students</header>
    <h2 class="section-title who">Who’s it for</h2>
    <div class="rows">
      <div class="row row--hs">
        <h3>HIGH SCHOOL GRADUATES</h3>
        <p class="body-copy">90% of high school grads aren't sure why they’re going to university or what they want to study.</p>
        <p class="body-copy">NMI helps students discover what they truly want to do in life, and make enormous progress towards these goals.</p>
        <div class="icon" role="img" aria-label="Illustration of a graduation cap and diploma"></div>
      </div>
      <div class="row row--ps">
        <h3>Post-secondary students</h3>
        <p class="body-copy">28% of students switch or drop out of their program because it wasn’t for them or they didn’t like it.</p>
        <p class="body-copy">Don't keep moving around or risk switching careers down the road – find out what sparks your passion with NMI.</p>
        <div class="icon" role="img" aria-label="Illustration of a university student"></div>
      </div>
      <div class="row row--grad">
        <h3>Post-secondary graduates</h3>
        <p class="body-copy">50% of graduates are unemployed or underemployed, 60% are in debt.</p>
        <p class="body-copy">NMI will help you get your dream job – our students won’t settle for anything less.</p>
        <div class="icon" role="img" aria-label="Illustration of a college graduate"></div>
      </div>
    </div>
    <div class="badges" aria-hidden="true"><span></span><span></span><span></span><span></span></div>
    <div class="apply">
      <h2 class="section-title">How to apply</h2>
      <p class="bar">We select high-potential young leaders with a desire to improve themselves and impact the world.</p>
      <p class="body-copy">We won’t ask you for your grades – we care more about your values and potential.</p>
      <p class="body-copy">Visit www.brv.institute to apply now</p>
      <div class="globe" role="img" aria-label="Illustration of a globe wearing a graduation cap"></div>
    </div>
  </article>
</section>

</body>
</html>
```